Holiday Club Flyer for 2026

Hi Ferncraft. We need a new flyer making for our holiday club for this year. You have made the last few which have always been good. This year the theme is space so please could you change the design to a space theme. The dates of the Holiday club are 28th, 29th and 30th October. It is the same venue, same timings and same activities that happen, we need the dates updating and the them of the flyer changing to space. I have attached last years flyer for you as a reminder.

```html
<!DOCTYPE html>
<html lang="en">
<head>
<meta charset="utf-8">
<title>Space Adventure Holiday Club Flyer</title>
<link href="https://fonts.googleapis.com/css2?family=Manrope:wght@400;500;600;700&family=Titan+One&display=swap" rel="stylesheet">
<style>
  :root {
    --paper: #ffffff;
    --space-deep: #0b0a1c;
    --space-mid: #2a1550;
    --space-violet: #4a2280;
    --nebula: #7a3cb0;
    --title-pink: #d35ef0;
    --white: #ffffff;
    --bubble: rgba(150, 80, 200, 0.55);
    --bubble-edge: rgba(200, 140, 240, 0.6);
    --label-box: rgba(110, 50, 160, 0.85);
    --ring-pink: #e0307a;
    --rocket-gold: #f4b63a;
    --moon: #c9bcd8;
  }
  * { margin: 0; padding: 0; box-sizing: border-box; }
  html, body { width: 1200px; height: 870px; overflow: hidden; background: var(--paper); }
  body { position: relative; font-family: "Manrope", sans-serif; color: var(--white); }

  .page { position: absolute; top: 69px; width: 520px; height: 736px; overflow: hidden; }
  .page--cover { left: 67px; background: linear-gradient(180deg, #05040d 0%, #1a1233 45%, #2a1a45 70%, #140c24 100%); }
  .page--info { left: 616px; background: linear-gradient(160deg, #3a2050 0%, var(--space-mid) 40%, #1a1640 70%, var(--space-violet) 100%); }

  .art { position: absolute; }
  .art--nebula { left: 0; top: 230px; width: 520px; height: 320px; background: radial-gradient(ellipse at 50% 50%, rgba(170,150,200,0.35) 0%, rgba(90,60,140,0.2) 50%, transparent 75%); }
  .art--astronaut { left: 71px; top: 90px; width: 85px; height: 127px; border-radius: 40%; background: radial-gradient(circle, #e9e9f0 0%, #9aa0b8 70%, transparent 100%); }
  .art--ringed-planet { left: 410px; top: 101px; width: 61px; height: 42px; border-radius: 50%; background: radial-gradient(circle, #d59ad0 0%, #8a5ac0 60%, transparent 100%); }
  .art--rocket { width: 58px; height: 40px; border-radius: 50%; background: radial-gradient(circle, var(--rocket-gold) 0%, #f07a2a 60%, transparent 100%); }
  .art--rocket-cover { left: 314px; top: 217px; }
  .art--rocket-info { left: 235px; top: 562px; width: 55px; height: 50px; }
  .art--satellite { left: 39px; top: 477px; width: 95px; height: 85px; border-radius: 30%; background: radial-gradient(circle, #9a98a8 0%, #555468 60%, transparent 100%); }
  .art--small-planet { left: 434px; top: 509px; width: 58px; height: 40px; border-radius: 50%; background: radial-gradient(circle, #c8c6d0 0%, #707080 60%, transparent 100%); }
  .art--moon { left: -140px; top: 580px; width: 800px; height: 500px; border-radius: 50%; background: radial-gradient(ellipse at 50% 10%, #e8dcf2 0%, var(--moon) 25%, #6a5a80 60%, #2a1e40 100%); box-shadow: 0 -20px 60px rgba(220,190,255,0.45); }
  .art--big-planet { left: 285px; top: -148px; width: 424px; height: 424px; border-radius: 50%; background: radial-gradient(circle at 30% 70%, #c060e0 0%, #7a30a8 40%, #3a1a5a 80%); opacity: 0.85; }
  .art--glow { left: 130px; top: 30px; width: 110px; height: 110px; border-radius: 50%; background: radial-gradient(circle, rgba(200,150,255,0.25) 0%, transparent 70%); }

  .title { position: absolute; left: 0; top: 0; overflow: visible; }
  .title__space { font-family: "Titan One", sans-serif; fill: var(--title-pink); }
  .title__adventure { font-family: "Titan One", sans-serif; fill: var(--white); }

  .brand { position: absolute; left: 15px; top: 16px; display: flex; align-items: center; gap: 7px; font-weight: 700; font-size: 13px; line-height: 1; }
  .brand__dot { width: 30px; height: 30px; border-radius: 50%; background: #1f9a3a; }
  .brand__name { width: 70px; }

  .label-arc { position: absolute; left: 0; top: 0; overflow: visible; font-family: "Manrope", sans-serif; font-weight: 600; font-size: 20px; fill: var(--white); }

  .bubble { position: absolute; width: 164px; height: 164px; border-radius: 50%; background: radial-gradient(circle at 45% 40%, rgba(170,100,220,0.55) 0%, var(--bubble) 60%, rgba(110,50,170,0.7) 100%); border: 2px solid var(--bubble-edge); box-shadow: 0 0 14px rgba(180,110,240,0.4); display: flex; flex-direction: column; align-items: center; justify-content: center; text-align: center; }
  .bubble--time { left: 16px; top: 215px; font-size: 14px; line-height: 1.15; }
  .bubble--date { left: 202px; top: 217px; font-size: 16px; font-weight: 500; gap: 12px; }
  .bubble__strong { font-weight: 700; font-size: 15px; margin: 3px 0 12px; }
  .bubble__strong:last-child { margin-bottom: 0; }

  .features { position: absolute; right: 0; top: 186px; display: flex; flex-direction: column; align-items: flex-end; }
  .features__heading { font-weight: 700; font-size: 17px; margin: 0 10px 8px 0; }
  .features__item { background: var(--label-box); font-size: 16px; padding: 0 10px; height: 28px; line-height: 28px; margin-bottom: 6px; }

  .contact { position: absolute; left: 30px; width: 420px; display: flex; align-items: center; }
  .contact__icon { width: 20px; height: 20px; flex: none; }
  .contact__rule { width: 1px; height: 38px; background: rgba(255,255,255,0.75); margin: 0 18px 0 19px; flex: none; }
  .contact__text { font-size: 12.5px; line-height: 1.35; }
  .contact__heading { font-size: 15px; font-weight: 600; }
  .contact__strong { font-size: 13px; font-weight: 700; }
  .contact--location { top: 408px; }
  .contact--register { top: 464px; }
  .contact--email { top: 516px; }

  .wave { position: absolute; left: 0; top: 0; }
  .rings { position: absolute; left: 0; top: 0; }

  .find-us { position: absolute; left: 364px; top: 535px; width: 160px; text-align: center; font-size: 13px; line-height: 18px; }

  .ages { position: absolute; left: 86px; top: 627px; width: 120px; display: flex; flex-direction: column; align-items: center; font-weight: 700; font-size: 17px; }
  .ages__box { background: var(--label-box); height: 27px; line-height: 27px; padding: 0 12px; }
  .ages__box--wide { width: 120px; text-align: center; }
  .ages__to { height: 30px; line-height: 30px; }
</style>
</head>
<body>

  <section class="page page--cover">
    <div class="art art--nebula" role="img" aria-label="Misty purple nebula clouds and star field"></div>
    <div class="art art--astronaut" role="img" aria-label="Illustrated astronaut floating on a tether"></div>
    <div class="art art--ringed-planet" role="img" aria-label="Illustrated striped ringed planet"></div>
    <div class="art art--rocket art--rocket-cover" role="img" aria-label="Illustrated yellow rocket"></div>
    <div class="art art--satellite" role="img" aria-label="Illustrated satellite"></div>
    <div class="art art--small-planet" role="img" aria-label="Illustrated grey ringed planet"></div>
    <div class="art art--moon" role="img" aria-label="Glowing lilac moon surface"></div>

    <svg class="title" width="520" height="736" viewBox="0 0 520 736">
      <path id="cover-space-path" d="M114 326 Q250 316 384 330" fill="none"/>
      <path id="cover-adv-path" d="M58 414 Q255 350 455 424" fill="none"/>
      <text class="title__space" font-size="64"><textPath href="#cover-space-path" textLength="268" lengthAdjust="spacingAndGlyphs">SPACE</textPath></text>
      <text class="title__adventure" font-size="52"><textPath href="#cover-adv-path" textLength="400" lengthAdjust="spacingAndGlyphs">ADVENTURE</textPath></text>
    </svg>
  </section>

  <section class="page page--info">
    <div class="art art--big-planet" role="img" aria-label="Large glowing purple planet"></div>
    <div class="art art--glow" role="img" aria-label="Faint glowing planet rings"></div>

    <div class="brand">
      <span class="brand__dot"></span>
      <span class="brand__name">Starlings holiday club</span>
    </div>

    <svg class="title" width="520" height="736" viewBox="0 0 520 736">
      <path id="info-space-path" d="M160 95 Q255 88 350 100" fill="none"/>
      <path id="info-adv-path" d="M124 162 Q262 98 394 168" fill="none"/>
      <text class="title__space" font-size="44"><textPath href="#info-space-path" textLength="188" lengthAdjust="spacingAndGlyphs">SPACE</textPath></text>
      <text class="title__adventure" font-size="40"><textPath href="#info-adv-path" textLength="290" lengthAdjust="spacingAndGlyphs">ADVENTURE</textPath></text>
    </svg>

    <svg class="label-arc" width="520" height="736" viewBox="0 0 520 736">
      <path id="time-path" d="M66 200 Q92 188 120 194" fill="none"/>
      <path id="date-path" d="M248 197 Q276 190 306 201" fill="none"/>
      <text><textPath href="#time-path">TIME</textPath></text>
      <text><textPath href="#date-path">DATE</textPath></text>
    </svg>

    <div class="bubble bubble--time">
      <span>Drop off from</span>
      <span class="bubble__strong">8:45 AM</span>
      <span>Collect your<br>children</span>
      <span class="bubble__strong">12:30 PM</span>
    </div>
    <div class="bubble bubble--date">
      <span>28th October</span>
      <span>29th October</span>
      <span>30th October</span>
    </div>

    <div class="features">
      <p class="features__heading">FEATURING</p>
      <p class="features__item">Games</p>
      <p class="features__item">Bible stories</p>
      <p class="features__item">quizzes</p>
      <p class="features__item">craft &amp; more!</p>
    </div>

    <div class="contact contact--location">
      <svg class="contact__icon" viewBox="0 0 20 20" aria-hidden="true"><path d="M10 1.5a6 6 0 0 0-6 6c0 4.5 6 11 6 11s6-6.5 6-11a6 6 0 0 0-6-6zm0 8.3a2.3 2.3 0 1 1 0-4.6 2.3 2.3 0 0 1 0 4.6z" fill="#fff"/></svg>
      <span class="contact__rule"></span>
      <p class="contact__text"><span class="contact__heading">LOCATION</span><br><span class="contact__strong">St Aldric's Church Marlowe Harrow Lane</span></p>
    </div>
    <div class="contact contact--register">
      <svg class="contact__icon" viewBox="0 0 20 20" aria-hidden="true"><path d="M9 3H5a2 2 0 0 0-2 2v10a2 2 0 0 0 2 2h10a2 2 0 0 0 2-2v-4" fill="none" stroke="#fff" stroke-width="1.8" stroke-linecap="round"/><path d="M15 2.5l2.5 2.5-7.5 7.5H7.5V10z" fill="none" stroke="#fff" stroke-width="1.8" stroke-linejoin="round"/></svg>
      <span class="contact__rule"></span>
      <p class="contact__text">REGISTER AT<br>https://staldrics.example/holiday-club</p>
    </div>
    <div class="contact contact--email">
      <svg class="contact__icon" viewBox="0 0 20 20" aria-hidden="true"><rect x="2" y="4.5" width="16" height="11" fill="none" stroke="#fff" stroke-width="1.4"/><path d="M2 4.5l8 6.5 8-6.5M2 15.5l6-5.5M18 15.5l-6-5.5" fill="none" stroke="#fff" stroke-width="1.4"/></svg>
      <span class="contact__rule"></span>
      <p class="contact__text">Email:<br>sam@staldrics.example</p>
    </div>

    <svg class="wave" width="520" height="736" viewBox="0 0 520 736" aria-hidden="true">
      <defs>
        <linearGradient id="wave-fill" x1="0" y1="0" x2="0" y2="1">
          <stop offset="0" stop-color="#5a2a8e"/>
          <stop offset="1" stop-color="#4a2080"/>
        </linearGradient>
      </defs>
      <path d="M0 585 Q40 570 120 605 Q200 625 250 610 Q280 640 270 690 Q262 720 290 736 L0 736 Z" fill="url(#wave-fill)"/>
    </svg>

    <div class="art art--rocket art--rocket-info" role="img" aria-label="Illustrated yellow rocket"></div>

    <svg class="rings" width="520" height="736" viewBox="0 0 520 736" aria-hidden="true">
      <circle cx="444" cy="575" r="82" fill="rgba(40,30,80,0.55)"/>
      <circle cx="442" cy="575" r="95" fill="none" stroke="var(--ring-pink)" stroke-width="2"/>
      <circle cx="440" cy="575" r="118" fill="none" stroke="var(--ring-pink)" stroke-width="2"/>
    </svg>

    <p class="find-us">Find Us:<br>St Aldric's Church<br>Harrow Lane<br>Marlowe, MW4 2QT</p>

    <div class="ages">
      <span class="ages__box ages__box--wide">RECEPTION</span>
      <span class="ages__to">TO</span>
      <span class="ages__box">YEAR&nbsp; 7</span>
    </div>
  </section>

</body>
</html>
```